Used Semi Truck Website Redesign

We are redoing the website backend and would like to also do a front end redesign. I would like a Mobile and Desktop mockup for each page. The website has more mobile visitors than desktop visitors. Our competitor is http://www.haulwaybazaar.example. We don't want to copy them exactly but we want a site that looks more like that. We need the functionality of that site. One big difference is that we also sell parts and trailers.

We need a redesign for front page, product detail page, search result page, content page. It is very important that the site is very easy to use on mobile devices. Our target audience is Truck drivers.

Feel free to use demo fonts stock images, and icons. We will purchase necessary 3rd party media when a winner is chosen.

Target Market(s)

People who want to buy used trucks.

Coding

Coded - Design and coding required

Number of Pages Required

5+ page

Requirements
Must have
• Mockup for Desktop and Mobile pages.

```html
<!DOCTYPE html>
<html lang="en">
<head>
<meta charset="utf-8">
<title>Ridgeline Trucks</title>
<link href="https://fonts.googleapis.com/css2?family=Open+Sans:wght@400;600;700;800&display=swap" rel="stylesheet">
<style>
:root{
  --orange:#ff7b00;
  --orange-dark:#e56f00;
  --ink:#333;
  --grey-text:#555;
  --tile:#f2f2f2;
  --band:#f4f4f4;
  --footer:#eeeeee;
  --bottom:#4a4a4a;
  --white:#fff;
  --icon:#8a8a8a;
}
*{box-sizing:border-box;margin:0;padding:0}
html,body{width:1200px;height:2344px;overflow:hidden;background:var(--white)}
body{font-family:"Open Sans",Arial,sans-serif;color:var(--ink);position:relative}
a{color:inherit;text-decoration:none}

.site-header{position:absolute;top:0;left:0;width:1200px;height:81px;background:linear-gradient(#fff,#f3f3f3)}
.brand{position:absolute;left:75px;top:20px;font-size:34px;font-weight:800;color:#555;letter-spacing:-.5px}
.main-nav{position:absolute;left:455px;top:25px;display:flex;gap:8px}
.main-nav a{display:block;height:33px;line-height:29px;border:2px solid var(--orange);border-radius:3px;font-size:14px;font-weight:700;color:#444;text-align:center;width:100px}
.main-nav a.wide{width:101px}
.user-links{position:absolute;top:32px;left:806px;display:flex;gap:34px;font-size:12px;font-weight:600;color:#444}
.user-links span{display:flex;align-items:center;gap:8px}
.user-links svg{width:11px;height:11px;fill:#444}

.quick-search{position:absolute;top:81px;left:0;width:1200px;height:116px;background:linear-gradient(90deg,#e57100,var(--orange) 30%,#f08000)}
.qs-label{position:absolute;left:75px;top:44px;color:#fff;font-size:18px;font-weight:700}
.field{position:absolute;height:34px;background:#fff;border-radius:2px;font-size:12px;color:#666;padding:0 10px;line-height:34px}
.field.select::after{content:"";position:absolute;right:12px;top:13px;width:5px;height:5px;border-right:1.5px solid #666;border-bottom:1.5px solid #666;transform:rotate(45deg)}
.search-btn{position:absolute;left:816px;top:20px;width:129px;height:74px;background:#222;color:#fff;font-size:18px;font-weight:700;text-align:center;line-height:74px;border-radius:2px}
.adv-link{position:absolute;left:984px;top:49px;color:#fff;font-size:13px;font-weight:700;text-decoration:underline}

.hero{position:absolute;top:197px;left:0;width:1200px;height:439px;background:linear-gradient(100deg,#5b5f62 0%,#8a9095 40%,#6d5d5a 62%,#9a9ea2 85%,#c9ccce 100%)}
.hero h1{position:absolute;left:75px;top:108px;color:#fff;font-size:64px;font-weight:800;letter-spacing:1px}
.hero p{position:absolute;left:75px;top:190px;color:#fff;font-size:36px;font-weight:700;line-height:42px}
.dots{position:absolute;left:75px;top:377px;display:flex;gap:6px}
.dots i{width:12px;height:12px;border-radius:50%;background:#fff}
.dots i.on{background:var(--orange)}

.categories{position:absolute;top:684px;left:75px;width:1050px;display:grid;grid-template-columns:331px 331px 331px;column-gap:29px;row-gap:30px}
.cat-tile{height:179px;background:var(--tile);text-align:center;padding-top:30px}
.cat-tile svg{height:68px;width:110px;fill:var(--icon)}
.cat-tile h3{margin-top:16px;color:var(--orange);font-size:17px;font-weight:700;line-height:22px;text-transform:uppercase}
.cat-tile.active{background:var(--orange)}
.cat-tile.active svg{fill:#fff}
.cat-tile.active h3{color:#fff}

.featured{position:absolute;top:1113px;left:0;width:1200px;height:564px;background:var(--band)}
.featured h2{position:absolute;top:44px;width:100%;text-align:center;font-size:21px;font-weight:700;color:#333}
.ad-cards{position:absolute;top:99px;left:75px;display:flex;gap:29px}
.ad-card{width:331px;height:319px;background:#fff;text-align:center}
.ad-photo{height:180px}
.ad-card h4{margin-top:22px;font-size:16px;font-weight:700;color:#222}
.ad-card .type{margin-top:6px;font-size:15px;color:#444}
.ad-card .price{margin-top:2px;font-size:15px;font-weight:700;color:var(--orange)}
.ad-card .loc{margin-top:2px;font-size:15px;color:#444}
.btn{position:absolute;top:471px;height:44px;width:244px;background:var(--orange);color:#fff;font-size:15px;font-weight:700;text-align:center;line-height:44px;border-radius:2px}

.news{position:absolute;top:1677px;left:0;width:1200px;height:351px}
.news h2{font-size:21px;font-weight:700;color:#333;position:absolute;top:36px}
.post,.tweet{position:absolute}
.post h3,.tweet h3{font-size:17px;font-weight:700;color:var(--orange)}
.post p,.tweet p{font-size:14px;line-height:21px;color:#555;margin-top:3px}
.post small{display:block;font-size:11px;margin-top:10px;color:#333}
.tweet{padding-left:46px}
.tweet .bird{position:absolute;left:0;top:4px;width:25px;height:25px;border-radius:50%;background:#8b98a6}
.tweet p a{color:var(--orange)}

.site-footer{position:absolute;top:2028px;left:0;width:1200px;height:263px;background:var(--footer)}
.f-col{position:absolute;top:50px}
.f-col h5{font-size:13px;font-weight:700;color:var(--orange);margin-bottom:10px}
.f-col a{display:block;font-size:13px;color:#555;line-height:31px}
.bottom-bar{position:absolute;top:2291px;left:0;width:1200px;height:53px;background:var(--bottom);color:#ddd;font-size:13px}
.bottom-bar .copy{position:absolute;left:75px;top:17px}
.social{position:absolute;left:961px;top:15px;display:flex;gap:17px}
.social i{width:22px;height:22px;background:#fff;border-radius:3px}
</style>
</head>
<body>

<header class="site-header">
  <div class="brand">Ridgeline <span style="color:#555">Trucks</span></div>
  <nav class="main-nav"><a href="#">FIND</a><a href="#">SELL</a><a href="#" class="wide">RESEARCH</a></nav>
  <div class="user-links">
    <span><svg viewBox="0 0 10 10"><rect x="1" y="4" width="8" height="6"/><path d="M3 4V3a2 2 0 014 0v1" stroke="#444" fill="none" stroke-width="1.4"/></svg>LOG IN</span>
    <span><svg viewBox="0 0 10 10"><rect x="0" y="0" width="10" height="10"/></svg>REGISTER</span>
    <span><svg viewBox="0 0 10 10"><circle cx="5" cy="3" r="2.5"/><path d="M0 10a5 4 0 0110 0z"/></svg>FIND A DEALER</span>
  </div>
</header>

<section class="quick-search">
  <div class="qs-label">QUICK SEARCH:</div>
  <div class="field" style="left:242px;top:20px;width:178px">Keyword</div>
  <div class="field select" style="left:242px;top:60px;width:178px">Select a Class</div>
  <div class="field select" style="left:434px;top:20px;width:179px">Select a Category</div>
  <div class="field select" style="left:434px;top:60px;width:179px">Select a Make</div>
  <div class="field" style="left:625px;top:20px;width:178px">Zip Code</div>
  <div class="field select" style="left:625px;top:60px;width:178px">Any Distance</div>
  <div class="search-btn">SEARCH</div>
  <a class="adv-link" href="#">ADVANCED SEARCH</a>
</section>

<section class="hero" role="img" aria-label="Photo of a red semi truck with a white trailer on a snowy mountain road">
  <h1>RIDGELINE TRUCKS</h1>
  <p>We sell used trucks &amp;<br>also parts, trailers</p>
  <div class="dots"><i class="on"></i><i></i><i></i><i></i></div>
</section>

<section class="categories">
  <a class="cat-tile active" href="#">
    <svg viewBox="0 0 110 68"><rect x="37" y="2" width="36" height="10"/><rect x="33" y="14" width="44" height="26"/><rect x="30" y="42" width="50" height="10"/><rect x="33" y="54" width="10" height="12"/><rect x="67" y="54" width="10" height="12"/></svg>
    <h3>Find Heavy Duty Trucks<br>for Sale</h3>
  </a>
  <a class="cat-tile" href="#">
    <svg viewBox="0 0 110 68"><rect x="35" y="6" width="50" height="44"/><path d="M10 50V30l8-12h14v32z"/><circle cx="22" cy="56" r="8"/><circle cx="72" cy="56" r="8"/></svg>
    <h3>Find Medium Duty Trucks<br>for Sale</h3>
  </a>
  <a class="cat-tile" href="#">
    <svg viewBox="0 0 110 68"><rect x="25" y="8" width="26" height="16"/><rect x="25" y="26" width="36" height="24"/><path d="M63 50V26h14l10 14v10z"/><circle cx="38" cy="56" r="7"/><circle cx="76" cy="56" r="7"/></svg>
    <h3>Find Light Duty Trucks<br>for Sale</h3>
  </a>
  <a class="cat-tile" href="#">
    <svg viewBox="0 0 110 68"><path d="M10 50V20l6-8h18v38z"/><rect x="34" y="44" width="66" height="6"/><circle cx="22" cy="56" r="7"/><circle cx="88" cy="56" r="7"/></svg>
    <h3>Find Truck Trailers<br>for Sale</h3>
  </a>
  <a class="cat-tile" href="#">
    <svg viewBox="0 0 110 68"><path d="M55 2a18 18 0 00-18 18c0 14 18 44 18 44s18-30 18-44A18 18 0 0055 2zm0 25a7 7 0 110-14 7 7 0 010 14z"/></svg>
    <h3>Trucks for Sale<br>by State</h3>
  </a>
  <a class="cat-tile" href="#">
    <svg viewBox="0 0 110 68"><path d="M32 56l30-30 8 8-30 30z"/><path d="M58 8a16 16 0 0020 20l-8 8-16-16z"/><path d="M34 10l10 4 26 26 4 10-10-4-26-26z" opacity=".9"/></svg>
    <h3>Trucks for Sale<br>by Make</h3>
  </a>
</section>

<section class="featured">
  <h2>FEATURED ADS</h2>
  <div class="ad-cards">
    <article class="ad-card">
      <div class="ad-photo" role="img" aria-label="Photo of a white passenger van" style="background:linear-gradient(#fff,#e6e6e6 70%,#fff)"></div>
      <h4>2016 Carver T350</h4><div class="type">Passenger Van</div><div class="price">$33,380.00</div><div class="loc">Alder Falls, IA</div>
    </article>
    <article class="ad-card">
      <div class="ad-photo" role="img" aria-label="Photo of a white semi truck on a highway" style="background:linear-gradient(#6f9ed6,#c9d6e2 55%,#7c8a6a 75%,#6a6a6a)"></div>
      <h4>2016 Carver T350</h4><div class="type">Passenger Van</div><div class="price">$33,380.00</div><div class="loc">Alder Falls, IA</div>
    </article>
    <article class="ad-card">
      <div class="ad-photo" role="img" aria-label="Photo of a white semi truck parked in a lot" style="background:linear-gradient(#9fc2e6,#e2e5e8 55%,#b3b3b0)"></div>
      <h4>2016 Carver T350</h4><div class="type">Passenger Van</div><div class="price">$33,380.00</div><div class="loc">Alder Falls, IA</div>
    </article>
  </div>
  <a class="btn" href="#" style="left:342px">View all Featured Trucks</a>
  <a class="btn" href="#" style="left:614px">Place your Listing Here</a>
</section>

<section class="news">
  <h2 style="left:75px">BLOG POSTS</h2>
  <article class="post" style="left:75px;top:96px;width:500px">
    <h3>Aliquam molestie, mi et imperdiet euismod</h3>
    <p>Dui purus auctor tellus, et interdum lacus lectus et ante. Sed accumsan sollicitudin sapien, sit amet adipiscing turpis gravida ac.</p>
    <small>Posted on Dec10, 2016</small>
  </article>
  <article class="post" style="left:75px;top:215px;width:500px">
    <h3>Aliquam molestie, mi et imperdiet euismod</h3>
    <p>Dui purus auctor tellus, et interdum lacus lectus et ante. Sed accumsan sollicitudin sapien, sit amet adipiscing turpis gravida ac.</p>
    <small>Posted on Dec10, 2016</small>
  </article>
  <h2 style="left:626px">RECENT TWEETS</h2>
  <article class="tweet" style="left:627px;top:96px;width:500px">
    <i class="bird"></i>
    <h3>Aliquam molestie@ imperdiet euismod</h3>
    <p>Dui purus auctor tellus, et interdum lacus lectus et ante accumsan sollicitudin <a href="#">social.example/status/8</a> adipiscing turpis gravida ac.</p>
  </article>
  <article class="tweet" style="left:627px;top:215px;width:500px">
    <i class="bird"></i>
    <h3>Aliquam molestie@ imperdiet euismod</h3>
    <p>Dui purus auctor tellus, et interdum lacus lectus et ante accumsan sollicitudin <a href="#">social.example/status/8</a> adipiscing turpis gravida ac.</p>
  </article>
</section>

<footer class="site-footer">
  <div class="f-col" style="left:75px"><h5>EXPLORE OUR SITE</h5><a>Trucks for Sale</a><a>Truck Resources</a><a>New Truck Models</a><a>Check Truck Prices</a></div>
  <div class="f-col" style="left:297px"><h5>SALE YOUR TRUCK</h5><a>Private Truck Sellers</a><a>Truck Dealers</a><a>Advertise with us</a></div>
  <div class="f-col" style="left:534px"><h5>ABOUT COMPANY</h5><a>HaulwayBazaar.example</a><a>Newsletter Sign Up</a><a>Site Map</a></div>
  <div class="f-col" style="left:808px"><h5>RESOURCE ADVERTISERS</h5><a>Insurance</a><a>Jobs &amp; Training</a><a>Vehicle History</a><a>Truck Bodies</a><a>Finance/Lease</a></div>
  <div class="f-col" style="left:941px;top:80px"><a>Truck Parts</a><a>Steel Buildings</a><a>Fuel Management</a><a>Shipping &amp; Transport</a></div>
</footer>

<div class="bottom-bar">
  <div class="copy">Copyright © 2016 Company Name. All Right Reserved</div>
  <div class="social"><i></i><i></i><i></i><i></i><i></i></div>
</div>

</body>
</html>
```